The logo name is "Harbor Skin". The name of the product will be "Cutaneous Comfort". This product is specifically formulated for amputees. Therefore under the product name it should state "for amputees". The catch phrase will be "Experience Harbor find Calmness"
These are the things we need on the label:
Logo, product name, "for amputees", "Experience Harbor find Calmness", Safe, Effective, Directions: spray on problem areas, no need to dry off. harborskin.example, Made in Canada, 500ml.
The MOST IMPORTANT and therefore the most prominent thing on this lable will be the LOGO! The second most prominent thing will be the word "Comfort" We want to keep it very plain, very simple, very unclutered. Keep in mind that this lable will be placed on a white bottle or have a white back ground. The 500ml white PE bottle with trigger sprayer will have a tear drop label. See attached die line (S-294).
We want to stay with the colours that goes with the colour scheme of the logo. See attached logo. Soft colours. We do not want a picture! We would like the lable to be classy and rich.
Updates
The logo name is "Harbor Skin". The name of the product will be "Cutaneous Comfort". This product is specificlly formulated for amputees. Therefore under the product name it should state "for amputees". The catch phrase will be "Experience Harbor find Calmness"
Logo, product name, "for amputees", catch phrase "Experience Harbor find Calmness", Clean, Safe, Effective, Directions: spray on problem areas, no need to dry off. Also Harbor Skin Corpation, harborskin.example, Made in Canada, 500ml.
We want to stay with the colour scheme of the logo. See attached logo. Soft colours. We do not want a picture! We would like the lable to be classy and rich.
This is the offical directive that came from the governing panal of this lable. This panal it not know where it wanted to take this lable that would represent this line until they review all of your submissions, thank you for all your talented hard work. But now it is clear it is time to regroup and hit this objective.
Project Deadline Extended
Reason: New restrictions on lable wording for this product.
Target Market(s)
Amputees and Parents of.
Industry/Entity Type
Product
Requirements
Must have
- Final product to be in a pdf or an illustrator file

```html
<!DOCTYPE html>
<html lang="en">
<head>
<meta charset="utf-8">
<title>Harbor Skin – Cutaneous Comfort Label</title>
<link href="https://fonts.googleapis.com/css2?family=Lobster&family=Nunito:ital,wght@0,600;0,700;0,800;1,800&family=Sniglet:wght@800&display=swap" rel="stylesheet">
<style>
  :root {
    --page-bg: #e6e6e6;
    --water-light: #a9dcf3;
    --water-mid: #4fa9d8;
    --water-deep: #1d6496;
    --water-dark: #123f63;
    --ink-white: #ffffff;
    --ink-navy: #173d6b;
    --ink-mist: #e4eef5;
    --mark-teal: #2fa38c;
  }

  * { box-sizing: border-box; margin: 0; padding: 0; }

  html, body {
    width: 1200px;
    height: 900px;
    overflow: hidden;
  }

  body {
    background: var(--page-bg);
    position: relative;
    font-family: "Nunito", sans-serif;
  }

  .label {
    position: absolute;
    left: 365px;
    top: 40px;
    width: 470px;
    height: 820px;
    overflow: hidden;
    background: var(--water-deep);
  }

  .label__water {
    position: absolute;
    inset: 0;
    background:
      radial-gradient(ellipse 70% 45% at 60% 25%, rgba(169, 220, 243, 0.85) 0%, rgba(169, 220, 243, 0) 70%),
      radial-gradient(ellipse 80% 30% at 50% 60%, rgba(140, 205, 236, 0.55) 0%, rgba(140, 205, 236, 0) 75%),
      linear-gradient(180deg, var(--water-light) 0%, var(--water-mid) 40%, var(--water-deep) 78%, var(--water-dark) 100%);
  }

  .label__surface {
    position: absolute;
    left: 0;
    right: 0;
    bottom: 0;
    height: 220px;
    background: linear-gradient(180deg, rgba(18, 63, 99, 0) 0%, rgba(18, 63, 99, 0.6) 55%, rgba(18, 63, 99, 0.8) 100%);
  }

  .brand {
    position: absolute;
    left: 0;
    right: 0;
    top: 175px;
    display: flex;
    justify-content: center;
    align-items: center;
    gap: 14px;
  }

  .brand__square {
    width: 50px;
    height: 50px;
    background: var(--mark-teal);
  }

  .brand__name {
    font-family: "Nunito", sans-serif;
    font-weight: 800;
    font-size: 52px;
    line-height: 1;
    color: var(--ink-white);
  }

  .product {
    position: absolute;
    left: 0;
    right: 0;
    top: 340px;
    text-align: center;
    transform: rotate(-6deg);
  }

  .product__first {
    display: block;
    margin-left: 110px;
    font-family: "Nunito", sans-serif;
    font-style: italic;
    font-weight: 800;
    font-size: 30px;
    color: var(--ink-white);
    text-shadow: 2px 2px 0 var(--ink-navy), 3px 4px 6px rgba(0, 0, 0, 0.4);
  }

  .product__name {
    display: block;
    margin-top: -6px;
    font-family: "Lobster", cursive;
    font-size: 104px;
    line-height: 1.05;
    color: var(--ink-white);
    text-shadow: 3px 3px 0 var(--ink-navy), 5px 6px 10px rgba(0, 0, 0, 0.45);
  }

  .product__audience {
    display: block;
    margin-left: 70px;
    font-family: "Sniglet", sans-serif;
    font-weight: 800;
    font-size: 28px;
    letter-spacing: 1px;
    color: var(--ink-white);
    text-shadow: 2px 2px 0 var(--ink-navy), 3px 4px 6px rgba(0, 0, 0, 0.4);
  }

  .details {
    position: absolute;
    left: 30px;
    right: 30px;
    bottom: 28px;
    display: flex;
    flex-direction: column;
    align-items: center;
    gap: 12px;
    text-align: center;
    color: var(--ink-mist);
  }

  .details__claims {
    font-weight: 800;
    font-size: 17px;
    letter-spacing: 3px;
    text-transform: uppercase;
  }

  .details__directions {
    font-weight: 600;
    font-size: 16px;
    line-height: 1.35;
  }

  .details__tagline {
    font-weight: 600;
    font-size: 27px;
    color: var(--ink-white);
    text-shadow: 0 2px 4px rgba(0, 0, 0, 0.6);
  }

  .details__facts {
    display: flex;
    justify-content: space-between;
    width: 100%;
    font-weight: 700;
    font-size: 14px;
  }

  .details__maker {
    font-weight: 600;
    font-size: 13px;
    opacity: 0.85;
  }
</style>
</head>
<body>
  <section class="label">
    <div class="label__water" role="img" aria-label="Splashing clear blue water with droplets and bubbles"></div>
    <div class="label__surface"></div>

    <div class="brand">
      <span class="brand__square"></span>
      <span class="brand__name">Harbor Skin</span>
    </div>

    <div class="product">
      <span class="product__first">Cutaneous</span>
      <span class="product__name">Comfort</span>
      <span class="product__audience">for amputees</span>
    </div>

    <div class="details">
      <p class="details__tagline">Experience Harbor find Calmness</p>
      <p class="details__claims">Clean · Safe · Effective</p>
      <p class="details__directions">Directions: spray on problem areas,<br>no need to dry off.</p>
      <div class="details__facts">
        <span>harborskin.example</span>
        <span>Made in Canada</span>
        <span>500ml</span>
      </div>
      <p class="details__maker">Harbor Skin Corpation</p>
    </div>
  </section>
</body>
</html>
```